Business card design for my company.
I would like the card's background colour to be black. You can also see our web site to get an idea of our brand. https://www.tmwhomecrafting.com.au/
- Name
- Email

```html
<!DOCTYPE html>
<html lang="en">
<head>
<meta charset="utf-8">
<title>TMW Home Crafting – Business Card</title>
<link rel="stylesheet" href="https://fonts.googleapis.com/css2?family=Roboto:wght@400;500;700&display=swap">
<style>
  :root {
    --bg: #b9b9b9;
    --card: #050505;
    --green: #1a9347;
    --white: #f2f2f2;
    --rule: #9a9a9a;
  }
  * { box-sizing: border-box; margin: 0; padding: 0; }
  html, body {
    width: 1200px; height: 802px; overflow: hidden;
    background: var(--bg);
    font-family: "Roboto", Arial, sans-serif;
  }
  .canvas {
    position: relative; width: 1200px; height: 802px;
  }
  .card {
    position: absolute; left: 320px;
    width: 560px; height: 320px;
    background: var(--card);
    border-radius: 22px;
    overflow: hidden;
    color: var(--white);
  }
  .card--front { top: 60px; }
  .card--back { top: 422px; }

  /* front */
  .wordmark {
    position: absolute; top: 40px; right: 52px;
    display: flex; align-items: center; gap: 10px;
    font-weight: 700; font-size: 22px; letter-spacing: 2px;
    color: var(--white);
  }
  .wordmark__square { width: 14px; height: 14px; background: var(--green); }
  .holder {
    position: absolute; left: 44px; top: 112px;
  }
  .holder__name { color: var(--green); font-weight: 700; font-size: 26px; }
  .holder__role { font-size: 15px; margin-top: 4px; }
  .divider {
    position: absolute; left: 44px; right: 44px; top: 184px;
    height: 1px; background: var(--rule);
  }
  .contacts {
    position: absolute; left: 44px; top: 200px;
    list-style: none; font-size: 14px; line-height: 24px;
  }
  .contacts li { display: flex; align-items: center; gap: 10px; }
  .contacts svg { width: 13px; height: 13px; fill: var(--green); }
  .address {
    position: absolute; right: 44px; top: 204px;
    text-align: right; font-size: 13px; line-height: 20px;
  }
  .edge-band {
    position: absolute; left: 0; bottom: 0; width: 560px; height: 12px;
  }

  /* back */
  .back-mark {
    position: absolute; inset: 0;
    display: flex; align-items: center; justify-content: center; gap: 18px;
    font-weight: 700; font-size: 40px; letter-spacing: 4px;
    color: var(--white);
  }
  .back-mark__square { width: 28px; height: 28px; background: var(--green); }
</style>
</head>
<body>
<main class="canvas">
  <section class="card card--front" aria-label="Card front with contact details">
    <div class="wordmark"><span class="wordmark__square"></span>TMW HOME CRAFTING</div>
    <div class="holder">
      <p class="holder__name">Daniel Hartley</p>
      <p class="holder__role">Owner</p>
    </div>
    <div class="divider"></div>
    <ul class="contacts">
      <li><svg viewBox="0 0 24 24"><path d="M6.6 10.8a15.1 15.1 0 0 0 6.6 6.6l2.2-2.2a1 1 0 0 1 1-.25 11.4 11.4 0 0 0 3.6.57 1 1 0 0 1 1 1V20a1 1 0 0 1-1 1A17 17 0 0 1 3 4a1 1 0 0 1 1-1h3.5a1 1 0 0 1 1 1c0 1.25.2 2.45.57 3.6a1 1 0 0 1-.25 1z"/></svg>(407) 555-0142</li>
      <li><svg viewBox="0 0 24 24"><path d="M2 5h20v14H2z M2 5l10 8 10-8" fill="var(--green)"/><path d="M3 6l9 7 9-7" fill="none" stroke="#050505" stroke-width="1.6"/></svg>info@tmwhomecrafting.com.au</li>
      <li><svg viewBox="0 0 24 24"><circle cx="12" cy="12" r="10"/><path d="M2 12h20M12 2c3 3 3 17 0 20M12 2c-3 3-3 17 0 20" fill="none" stroke="#050505" stroke-width="1.4"/></svg>www.tmwhomecrafting.com.au</li>
    </ul>
    <p class="address">421, Address line goes here<br>45452, Country name</p>
    <svg class="edge-band" viewBox="0 0 560 12" preserveAspectRatio="none" aria-hidden="true">
      <polygon points="0,0 250,0 244,12 0,12" fill="var(--white)"/>
      <polygon points="254,0 560,0 560,12 248,12" fill="var(--green)"/>
    </svg>
  </section>

  <section class="card card--back" aria-label="Card back with company name">
    <div class="back-mark"><span class="back-mark__square"></span>TMW HOME CRAFTING</div>
  </section>
</main>
</body>
</html>
```